Corporate Design für Malermeister
Zielgruppe
Ich bin Malermeister ,
wir bieten komplettrenovierungen an vom Gestalten der Oberflächen, kreative Wandgestaltung Trockenbau, Bodenverlegearbeiten Parkett, Laminat, Teppich, designböden etc.
Fokus liegt bei den Malerarbeiten! Auch Fassaden werden restaurariert und gestaltet
Wir wollen modern und hochwertig rüber kommen
Aufgabenstellung
Das Logo soll zeigen, dass wir ein moderner kreativer Betrieb sind
da wir eine Diesntaleistung anbieten sollte es auch auf Vertrauen asutrahlen

```html
<!DOCTYPE html>
<html lang="de">
<head>
<meta charset="utf-8">
<title>Knickfalz – Briefbogen Farbhof</title>
<link href="https://fonts.googleapis.com/css2?family=Noto+Sans:wght@300;400;500;600;700&display=swap" rel="stylesheet">
<style>
  :root {
    --stage: #fafafa;
    --paper: #ffffff;
    --ink: #111111;
    --muted: #555555;
    --title: #6b6b6b;
    --brand-blue: #3a8ac0;
    --contact-blue: #1f6fba;
    --fold-line: #c8c8c8;
    --margin-red: #d0141c;
    --frame: #222222;
  }
  * { margin: 0; padding: 0; box-sizing: border-box; }
  html, body { width: 1200px; height: 1200px; overflow: hidden; }
  body {
    background: var(--stage);
    font-family: "Noto Sans", sans-serif;
    color: var(--ink);
    position: relative;
  }
  .sheet-title {
    position: absolute; top: 240px; left: 0; width: 1178px;
    text-align: center; font-weight: 300; font-size: 31px;
    color: var(--title);
  }
  .letterhead {
    position: absolute; left: 288px; top: 342px;
    width: 604px; height: 496px; overflow: hidden;
    background: var(--paper);
  }
  .margin-rule {
    position: absolute; left: 0; top: 0; width: 2px; height: 100%;
    background: var(--margin-red);
  }
  .frame {
    position: absolute; left: 3px; top: 2px; right: 5px; bottom: -2px;
    border: 1px solid var(--frame); border-bottom: none;
  }
  .edge {
    position: absolute; top: 0; right: 0; width: 3px; height: 100%;
    background: #444;
  }
  .fold-line {
    position: absolute; left: 2px; right: 0; top: 298px;
    border-top: 1px solid var(--fold-line);
  }
  .brand {
    position: absolute; left: 410px; top: 96px;
    display: flex; align-items: center; gap: 7px;
  }
  .brand-dot { width: 12px; height: 12px; border-radius: 50%; background: var(--brand-blue); }
  .brand-name {
    font-weight: 600; font-size: 25px; color: var(--brand-blue); line-height: 1;
  }
  .brand-trade {
    position: absolute; left: 410px; top: 129px;
    font-weight: 700; font-size: 11px; letter-spacing: 0.6px; color: #444;
  }
  .brand-claim {
    position: absolute; left: 410px; top: 145px;
    font-size: 9.4px; color: var(--muted);
  }
  .sender-line {
    position: absolute; left: 69px; top: 148px; font-size: 6.6px; color: #333;
  }
  .recipient {
    position: absolute; left: 69px; top: 175px; font-size: 11px; line-height: 14.5px;
    font-weight: 500; font-style: normal;
  }
  .contact { position: absolute; left: 410px; top: 172px; font-size: 8.4px; font-weight: 600; color: #444; }
  .contact-row { position: absolute; left: 0; line-height: 13px; }
  .contact-row svg { width: 11px; height: 11px; margin-top: 1px; fill: var(--contact-blue); display: block; }
  .contact-text { position: absolute; left: 16px; white-space: nowrap; line-height: 13px; }
  .contact-name { color: var(--contact-blue); font-size: 10px; font-weight: 700; }
  .contact-role { font-size: 7.8px; }
  .contact-web { color: var(--contact-blue); font-weight: 700; }
  .letter-date { position: absolute; left: 403px; top: 303px; font-size: 11px; }
  .letter-body {
    position: absolute; left: 67px; top: 356px; width: 492px;
    font-size: 10.1px; line-height: 14.4px;
  }
  .letter-body p { margin-bottom: 14.4px; }
</style>
</head>
<body>
  <h1 class="sheet-title">Knickfalz</h1>

  <section class="letterhead" aria-label="Briefbogen Farbhof">
    <div class="margin-rule"></div>
    <div class="frame"></div>
    <div class="edge"></div>

    <div class="brand">
      <span class="brand-dot"></span>
      <span class="brand-name">Farbhof</span>
    </div>
    <div class="brand-trade">MALERMEISTERBETRIEB</div>
    <div class="brand-claim">Farbe mit Sorgfalt | Räume mit Charakter</div>

    <div class="sender-line">Farbhof &nbsp;|&nbsp; Lindenweg 12 &nbsp;|&nbsp; 48211 Feldhain</div>

    <address class="recipient">
      Max Mustermann<br>Musterstraße 7<br>24536 Musterstadt
    </address>

    <div class="contact">
      <div class="contact-text contact-name" style="top:0">Lukas Vennert</div>
      <div class="contact-text contact-role" style="top:11px">Malermeister</div>

      <div class="contact-row" style="top:33px">
        <svg viewBox="0 0 12 12"><path d="M6 1 0.5 6h1.7v5h3v-3h1.6v3h3V6h1.7z"/></svg>
      </div>
      <div class="contact-text" style="top:33px">Lindenweg 12<br>48211 Feldhain</div>

      <div class="contact-row" style="top:72px">
        <svg viewBox="0 0 12 12"><path d="M3.5 0.5h5a1 1 0 0 1 1 1v9a1 1 0 0 1-1 1h-5a1 1 0 0 1-1-1v-9a1 1 0 0 1 1-1zm0.6 1.4v7.2h3.8V1.9z"/></svg>
      </div>
      <div class="contact-text" style="top:72px">0160 - 482 17 39</div>

      <div class="contact-row" style="top:85px">
        <svg viewBox="0 0 12 12"><path d="M0.5 2h11v8h-11zM1.5 3v0.6L6 6.7l4.5-3.1V3L6 6z"/></svg>
      </div>
      <div class="contact-text" style="top:85px">maler@farbhof.de</div>

      <div class="contact-row" style="top:98px">
        <svg viewBox="0 0 12 12"><circle cx="6" cy="6" r="5.3"/><path d="M3 4h3v2H4zM7 7h2v2H7z" fill="#fff"/></svg>
      </div>
      <div class="contact-text contact-web" style="top:98px">www.farbhof.de</div>
    </div>

    <div class="fold-line"></div>

    <div class="letter-date">Musterdorf, 07. Januar 2018</div>

    <div class="letter-body">
      <p>Sehr geehrter Herr Musterschüler,</p>
      <p>Eine wunderbare Heiterkeit hat meine ganze Seele eingenommen, gleich den süßen Frühlingsmorgen, die ich mit ganzem Herzen genieße. Ich bin allein und freue mich meines Lebens in dieser Gegend, die für solche Seelen geschaffen ist wie die meine. Ich bin so glücklich, mein Bester, so ganz in dem Gefühle von ruhigem Dasein versunken, daß meine Kunst darunter leidet. Ich könnte jetzt nicht zeichnen, nicht einen Strich, und bin nie ein größerer Maler gewesen als in diesen Augenblicken.</p>
      <p>Wenn das liebe Tal um mich dampft, und die hohe Sonne an der Oberfläche der undurchdringlichen Finsternis meines Waldes ruht, und nur einzelne Strahlen sich in das innere Heiligtum stehlen, ich</p>
    </div>
  </section>
</body>
</html>
```